New Business Card Design Project

Use the flyer uploaded and website www.brightoakbuilders.com for inspiration.
List Our Services on Backside of business cards
Marcus Delling
Harborline Builders Inc.
Licensed General Contractors
858-471-6093

Contact Information for Business Card

Use the flyer uploaded and website www.brightoakbuilders.com for inspiration. List Our Services on Backside of business cards Marcus Delling Harborline Builders Inc. Licensed General Contractors 858-471-6093

```html
<!DOCTYPE html>
<html lang="en">
<head>
<meta charset="utf-8">
<title>Harborline Builders – Business Card</title>
<link href="https://fonts.googleapis.com/css2?family=Playfair+Display:wght@400;700&family=Open+Sans:wght@400&display=swap" rel="stylesheet">
<style>
  :root {
    --backdrop: #3a332e;
    --card: #161616;
    --card-edge: #222222;
    --ink: #e6e6e6;
    --ink-soft: #bdbdbd;
    --rule: #8a8a8a;
  }
  * { margin: 0; padding: 0; box-sizing: border-box; }
  html, body {
    width: 1200px; height: 716px; overflow: hidden;
    background: var(--backdrop);
  }
  .canvas {
    position: relative; width: 1200px; height: 716px;
  }
  .card {
    position: absolute; top: 210px;
    width: 520px; height: 297px;
    background: var(--card);
    border: 1px solid var(--card-edge);
    border-radius: 6px;
    box-shadow: 0 10px 30px rgba(0,0,0,.45);
    color: var(--ink);
  }
  .card--front { left: 50px; }
  .card--back { left: 630px; }

  .brand {
    display: flex; align-items: center; gap: 10px;
    font-family: "Playfair Display", serif;
    font-weight: 400; letter-spacing: 2px;
    color: var(--ink);
    text-transform: uppercase;
  }
  .brand__mark {
    width: 10px; height: 10px; border: 1px solid var(--ink);
  }
  .card--front .brand {
    position: absolute; left: 0; right: 0; top: 132px;
    justify-content: center; font-size: 26px;
  }

  .card--back .brand {
    position: absolute; left: 24px; top: 104px;
    font-size: 17px; letter-spacing: 1.5px;
  }
  .divider {
    position: absolute; left: 262px; top: 70px;
    width: 1px; height: 120px; background: var(--rule);
  }
  .contact {
    position: absolute; left: 276px; top: 72px;
    font-family: "Open Sans", sans-serif;
  }
  .contact__name {
    font-family: "Playfair Display", serif;
    font-weight: 700; font-size: 17px; letter-spacing: 1px;
    text-transform: uppercase;
  }
  .contact__role {
    font-family: "Playfair Display", serif;
    font-size: 12px; line-height: 1.25; color: var(--ink-soft);
    margin-bottom: 8px;
  }
  .contact__line {
    display: flex; align-items: center; gap: 7px;
    font-size: 13px; line-height: 1.55;
  }
  .contact__line svg { width: 12px; height: 12px; flex: none; }
  .services {
    position: absolute; left: 0; right: 0; top: 214px;
    font-family: "Open Sans", sans-serif;
    font-size: 12.5px; line-height: 1.6; text-align: center;
  }
</style>
</head>
<body>
<main class="canvas">
  <section class="card card--front" aria-label="Card front">
    <div class="brand"><span class="brand__mark"></span>Harborline Builders</div>
  </section>

  <section class="card card--back" aria-label="Card back">
    <div class="brand"><span class="brand__mark"></span>Harborline Builders</div>
    <div class="divider"></div>
    <div class="contact">
      <p class="contact__name">Marcus Delling</p>
      <p class="contact__role">Harborline Builders Inc.<br>Licensed General Contractors</p>
      <p class="contact__line">
        <svg viewBox="0 0 24 24" fill="var(--ink)"><path d="M6.6 10.8a15.1 15.1 0 0 0 6.6 6.6l2.2-2.2c.3-.3.7-.4 1-.2 1.1.4 2.3.6 3.6.6.6 0 1 .4 1 1V20c0 .6-.4 1-1 1A17 17 0 0 1 3 4c0-.6.4-1 1-1h3.5c.6 0 1 .4 1 1 0 1.3.2 2.5.6 3.6.1.3 0 .7-.2 1z"/></svg>
        858-471-6093
      </p>
      <p class="contact__line">
        <svg viewBox="0 0 24 24" fill="none" stroke="var(--ink)" stroke-width="2"><rect x="3" y="5" width="18" height="14"/><path d="M3 5l9 8 9-8"/></svg>
        info@brightoakbuilders.com
      </p>
      <p class="contact__line">
        <svg viewBox="0 0 24 24" fill="none" stroke="var(--ink)" stroke-width="2"><circle cx="12" cy="12" r="9"/><path d="M3 12h18M12 3c3 3 3 15 0 18M12 3c-3 3-3 15 0 18"/></svg>
        www.brightoakbuilders.com
      </p>
    </div>
    <p class="services">
      &bull; Painting &bull; Flooring &bull; Kitchens<br>
      &bull; Bathrooms &bull; Energy Efficient Upgrades &bull; Custom Renovations
    </p>
  </section>
</main>
</body>
</html>
```